Website for Excavator and Earthworks Company

We require a modern, sleek and practical website for our newly created earthworks/excavator business in Perth, Western Australia called Bluegum Ridge Earthworks.

The website should have a modern, cutting edge feel but only needs to be relatively simplistic in it's layout and eventual functionality.

Some pages it should have would be Home, About, Projects and Contact Us.

```html
<!DOCTYPE html>
<html lang="en">
<head>
<meta charset="utf-8">
<title>Bluegum Ridge Earthworks</title>
<link href="https://fonts.googleapis.com/css2?family=Outfit:wght@400;500;600;700&display=swap" rel="stylesheet">
<style>
:root{
  --yellow:#d8dc00;
  --black:#0b0b0b;
  --dark:#1c1c1c;
  --mid:#2b2b2b;
  --white:#ffffff;
  --grey:#cfcfcf;
}
*{box-sizing:border-box;margin:0;padding:0}
html,body{width:1200px;height:4147px;overflow:hidden;background:var(--dark)}
body{font-family:"Outfit",sans-serif;color:var(--white);position:relative}
.abs{position:absolute}
.heading{font-weight:600;font-size:46px;letter-spacing:.5px;text-align:center;width:100%}
.heading span{color:var(--yellow)}
.kicker{font-size:15px;letter-spacing:7px;text-align:center;width:100%;display:flex;justify-content:center;align-items:center;gap:14px;color:var(--grey)}
.kicker::before,.kicker::after{content:"";width:30px;height:2px;background:var(--grey)}
.btn{background:var(--yellow);color:var(--black);font-weight:600;font-size:17px;display:flex;align-items:center;justify-content:center}

/* header */
.topbar{left:427px;top:0;width:773px;height:40px;background:var(--yellow);color:var(--black);font-size:14px;font-weight:500;display:flex;align-items:center;gap:44px;padding-left:40px}
.social{display:flex;gap:10px}
.social i{width:11px;height:11px;border-radius:50%;background:var(--black);display:block}
.nav{left:0;top:40px;width:1200px;height:82px;background:var(--black)}
.nav ul{list-style:none;position:absolute;left:416px;top:0;height:82px;display:flex;align-items:center;gap:40px;font-size:15px}
.nav li.active{color:var(--yellow);font-weight:600}
.nav .cta{background:var(--yellow);color:var(--black);padding:12px 14px;font-weight:600;margin-left:-10px}
.brand{left:88px;top:0;width:292px;height:182px;background:var(--black);clip-path:polygon(0 0,100% 0,100% 78%,92% 100%,8% 100%,0 78%);display:flex;flex-direction:column;align-items:center;justify-content:center;gap:8px}
.brand .mark{width:44px;height:44px;background:var(--yellow)}
.brand .name{font-weight:700;font-size:24px;color:var(--white);letter-spacing:1px}

/* hero */
.hero{left:0;top:122px;width:1200px;height:630px;background:linear-gradient(180deg,#6b7c8a 0%,#c9874a 40%,#8a5a30 75%,#3c2a1c 100%)}
.hero-text{left:0;top:150px;width:1200px;text-align:center}
.hero h1{font-size:58px;font-weight:700;line-height:60px;text-shadow:0 2px 6px rgba(0,0,0,.5)}
.hero .sub{font-size:17px;font-weight:600;margin-top:22px}
.hero .tag{font-size:15px;margin-top:20px}
.hero .btn{left:528px;top:372px;width:157px;height:55px}

/* about */
.about{left:0;top:752px;width:1200px;height:700px;background:linear-gradient(135deg,#252525,#151515)}
.about .badge{left:0;top:120px;width:545px;height:350px;display:flex;align-items:center;justify-content:center}
.about .badge span{font-size:90px;font-weight:700;color:var(--yellow);line-height:92px;text-align:center}
.about h2{left:632px;top:92px;font-size:46px;font-weight:600}
.about h2 span{color:var(--yellow)}
.about .sub{left:632px;top:150px;font-size:14px;letter-spacing:6px;color:var(--grey);display:flex;align-items:center;gap:6px}
.about .sub::after{content:"";width:60px;height:2px;background:var(--grey)}
.about .copy{left:632px;top:180px;width:456px;font-size:15px;line-height:25.7px;color:var(--grey);text-align:justify}
.about .copy p+p{margin-top:26px}
.about .btn{left:632px;top:477px;width:148px;height:53px}

/* services */
.services{left:0;top:1379px;width:1200px;height:764px;background:linear-gradient(180deg,#1a1a1a,#333 60%,#2a2a2a)}
.services .heading{position:absolute;top:160px}
.services .kicker{position:absolute;top:220px}
.card{top:293px;width:300px;height:290px}
.card .photo{width:100%;height:100%}
.card .label{position:absolute;left:28px;top:258px;width:245px;height:64px;background:var(--black);clip-path:polygon(0 0,100% 0,92% 100%,0 100%);font-size:17px;line-height:24px;text-align:center;display:flex;align-items:center;justify-content:center}
.arrow{top:438px;width:44px;height:44px;border:2px solid var(--white);border-radius:50%}
.band{background:var(--yellow)}

/* why */
.why{left:0;top:2143px;width:1200px;height:802px;background:var(--dark)}
.why .heading{position:absolute;top:105px}
.why .kicker{position:absolute;top:167px}
.benefit{width:330px}
.benefit h3{font-size:16px;font-weight:600;line-height:24px}
.benefit p{font-size:12px;line-height:25px;color:var(--grey)}
.right-align{text-align:right}

/* contact */
.contact{left:0;top:2945px;width:1200px;height:700px;background:linear-gradient(180deg,#262626,#1b1b1b)}
.contact .heading{position:absolute;top:85px}
.contact .kicker{position:absolute;top:148px}
.contact .intro{left:111px;top:210px;width:400px;font-size:15px;line-height:28px}
.info{left:111px;display:flex;gap:14px}
.info .dot{width:62px;height:62px;border-radius:50%;background:var(--yellow);flex:none;display:flex;align-items:center;justify-content:center}
.info h4{font-size:17px;font-weight:500;margin-top:4px}
.info p{font-size:15px;line-height:26px}
.form{left:599px;top:219px;width:490px;height:398px;background:var(--yellow)}
.field{position:absolute;background:var(--white);color:#555;font-size:14px;display:flex;align-items:flex-start;padding:13px 12px;gap:10px}
.field i{width:12px;height:12px;background:#999;border-radius:50%;display:block;flex:none;margin-top:2px}
.submit{position:absolute;left:38px;top:319px;width:148px;height:53px;background:var(--black);color:var(--white);font-weight:600;font-size:16px;display:flex;align-items:center;justify-content:center}

/* footer */
.footer{left:0;top:3749px;width:1200px;height:398px;background:var(--black)}
.footer .brand-f{left:111px;top:70px;width:290px;display:flex;flex-direction:column;align-items:center;gap:14px}
.footer .brand-f .mark{width:70px;height:70px;background:var(--yellow)}
.footer .brand-f .name{font-size:28px;font-weight:700}
.col{top:65px}
.col h5{font-size:21px;font-weight:500;margin-bottom:18px}
.col ul{list-style:none;font-size:14px}
.col li{height:34.5px;display:flex;align-items:center;gap:8px}
.col li::before{content:"➜";font-size:13px}
.fc{display:flex;gap:12px;align-items:center;font-size:14px;line-height:22px;margin-bottom:16px}
.fc .dot{width:30px;height:30px;border-radius:50%;background:var(--yellow);flex:none}
.footer .rule{left:111px;top:304px;width:978px;height:1px;background:#444}
.footer .copy{left:0;top:340px;width:1200px;text-align:center;font-size:15px}
</style>
</head>
<body>

<!-- Header -->
<div class="abs nav">
  <ul>
    <li class="active">HOME</li><li>ABOUT</li><li>SERVICES</li><li>WHY CHOOSE US</li><li>REVIEWS</li><li class="cta">CONTACT US</li>
  </ul>
</div>
<div class="abs topbar">
  <div class="social"><i></i><i></i><i></i><i></i></div>
  <div>CALL US: +61 8 9400 1200</div>
  <div>MAIL US: info@bluegumridge.example</div>
</div>
<div class="abs brand">
  <div class="mark"></div>
  <div class="name">BLUEGUM RIDGE</div>
</div>

<!-- Hero -->
<section class="abs hero" role="img" aria-label="Photo of excavators digging earth at sunset"></section>
<div class="abs hero-text hero" style="background:none;top:272px;height:auto">
  <h1>EXPERT EXCAVATION<br>&amp; EARTHWORKS</h1>
  <div class="sub">PROFESSIONAL EARTHMOVING SERVICES ACROSS PERTH, WA</div>
  <div class="tag">Reliable. Precise. Built for the Toughest Jobs.</div>
</div>
<div class="abs btn" style="left:528px;top:494px;width:157px;height:55px">GET STARTED</div>

<!-- About -->
<section class="abs about">
  <div class="abs badge"><span>BLUEGUM<br>RIDGE</span></div>
  <h2 class="abs">ABOUT <span>BLUEGUM RIDGE</span></h2>
  <div class="abs sub">EARTHWORKS</div>
  <div class="abs copy">
    <p>Bluegum Ridge Earthworks is a Perth-based excavation and earthmoving company delivering high-precision, professional services for residential, commercial, and industrial projects.</p>
    <p>We combine modern machinery, expert operators, and a safety-first approach to ensure every job is completed efficiently and to the highest standard. Duis aute irure dolor in reprehenderit in voluptate velit esse cillum dolore eu fugiat nulla pariatur. Excepteur sint occaecat cupidatat non ui officia deserunt mollit anim id est laborum.</p>
  </div>
  <div class="abs btn" style="left:632px;top:477px;width:148px;height:53px">READ MORE</div>
</section>

<!-- Hero/about transition shapes -->
<svg class="abs" style="left:0;top:649px" width="1200" height="110" viewBox="0 0 1200 110">
  <polygon points="797,58 850,0 1200,0 1200,55" fill="#d8dc00"/>
  <polygon points="0,58 560,58 520,103 0,103" fill="#d8dc00"/>
  <polygon points="560,58 1200,55 1200,110 520,110" fill="#202020"/>
</svg>

<!-- Services -->
<section class="abs services">
  <h2 class="heading">OUR <span>SERVICES</span></h2>
  <div class="kicker">OFFER</div>
  <div class="abs arrow" style="left:25px"><svg width="40" height="40" viewBox="0 0 40 40"><path d="M23 13 16 20l7 7" stroke="#fff" stroke-width="2.5" fill="none"/></svg></div>
  <div class="abs arrow" style="left:1130px"><svg width="40" height="40" viewBox="0 0 40 40"><path d="M17 13l7 7-7 7" stroke="#fff" stroke-width="2.5" fill="none"/></svg></div>
  <div class="abs card" style="left:111px">
    <div class="photo" role="img" aria-label="Close-up of an excavator bucket digging soil" style="background:linear-gradient(160deg,#8a6a4a,#5a4030 60,#3a2a1c)"></div>
    <div class="label">Precision residential<br>excavation</div>
  </div>
  <div class="abs card" style="left:451px">
    <div class="photo" role="img" aria-label="Excavator working on a commercial building site" style="background:linear-gradient(180deg,#bfcad2,#9b8a76 55%,#6a5040)"></div>
    <div class="label">Commercial and industrial<br>site works</div>
  </div>
  <div class="abs card" style="left:789px">
    <div class="photo" role="img" aria-label="Excavator digging a trench for footings" style="background:linear-gradient(180deg,#a8c6d8,#b07a4a 50%,#6a4428)"></div>
    <div class="label">Site cuts, trenching<br>&amp; footings</div>
  </div>
</section>
<svg class="abs" style="left:0;top:2089px" width="1200" height="54" viewBox="0 0 1200 54">
  <polygon points="0,0 600,0 650,54 0,54" fill="#d8dc00"/>
</svg>

<!-- Why choose us -->
<section class="abs why">
  <h2 class="heading">WHY <span>CHOOSE US</span></h2>
  <div class="kicker">BENEFITS</div>
  <svg class="abs" style="left:376px;top:244px" width="440" height="440" viewBox="0 0 440 440">
    <circle cx="220" cy="220" r="201" fill="none" stroke="#d8dc00" stroke-width="1.5" stroke-dasharray="6 5"/>
    <circle cx="220" cy="220" r="122" fill="none" stroke="#d8dc00" stroke-width="3"/>
    <text x="220" y="212" text-anchor="middle" font-family="Outfit,sans-serif" font-weight="700" font-size="34" fill="#d8dc00">BLUEGUM</text>
    <text x="220" y="250" text-anchor="middle" font-family="Outfit,sans-serif" font-weight="700" font-size="34" fill="#d8dc00">RIDGE</text>
  </svg>
  <svg class="abs" style="left:0;top:0" width="1200" height="802" viewBox="0 0 1200 802">
    <g fill="#d8dc00" stroke="#1c1c1c" stroke-width="3">
      <circle cx="462" cy="312" r="40"/><circle cx="733" cy="312" r="40"/>
      <circle cx="400" cy="464" r="40"/><circle cx="799" cy="464" r="40"/>
      <circle cx="459" cy="629" r="40"/><circle cx="727" cy="629" r="40"/>
    </g>
    <g fill="#111">
      <rect x="450" y="300" width="24" height="24" transform="rotate(45 462 312)"/>
      <rect x="720" y="304" width="26" height="16"/>
      <path d="M400 450l14 8-14 22-14-22z"/>
      <rect x="788" y="450" width="20" height="28"/>
      <path d="M446 644l12-26 14 26z"/>
      <circle cx="727" cy="629" r="14"/>
    </g>
  </svg>
  <div class="abs benefit right-align" style="left:70px;top:268px"><h3>Transparent Pricing &amp; Clear<br>Communication</h3><p>Excepteur sint occaident, sunt in culpa</p></div>
  <div class="abs benefit" style="left:788px;top:268px"><h3>Modern, High-Performance Machinery</h3><p>Excepteur sint occaecat cupidatat non proident, sunt<br>in culpa qui officia deserunt.</p></div>
  <div class="abs benefit right-align" style="left:8px;top:424px"><h3>Safety-First, Fully Insured<br>Operations</h3><p>Excepteur sint occaident, sunt in culpa</p></div>
  <div class="abs benefit" style="left:855px;top:424px"><h3>Skilled &amp; Certified Operators</h3><p>Excepteur sint occaecat cupidatat non<br>p in culpa qui officia deserunt.</p></div>
  <div class="abs benefit right-align" style="left:67px;top:587px"><h3>Precision Earthworks for Any Scale</h3><p>Excepteur sint occaecat cupidatat non proident, sunt<br>in culpa qui officia deserunt.</p></div>
  <div class="abs benefit" style="left:781px;top:587px"><h3>Reliable &amp; On-Time Delivery</h3><p>Excepteur sint occaecat cupidatat non proident, sunt<br>in culpa qui officia deserunt.</p></div>
</section>

<!-- Contact -->
<section class="abs contact">
  <h2 class="heading">GET IN <span>TOUCH WITH US</span></h2>
  <div class="kicker">CONTACT US</div>
  <p class="abs intro">Call us or schedule a call, video meeting, or mobile visit. We're here to help and answer any financial question you might have.</p>
  <div class="abs info" style="top:322px">
    <div class="dot"><svg width="24" height="24" viewBox="0 0 24 24"><path d="M12 2a7 7 0 0 0-7 7c0 5 7 13 7 13s7-8 7-13a7 7 0 0 0-7-7zm0 10a3 3 0 1 1 0-6 3 3 0 0 1 0 6z" fill="#111"/></svg></div>
    <div><h4>LOCATION</h4><p>42 Quarry Road Canning Vale<br>WA 6155</p></div>
  </div>
  <div class="abs info" style="top:436px">
    <div class="dot"><svg width="24" height="24" viewBox="0 0 24 24"><path d="M6.6 10.8a15 15 0 0 0 6.6 6.6l2.2-2.2a1 1 0 0 1 1-.25 11 11 0 0 0 3.6.6 1 1 0 0 1 1 1V20a1 1 0 0 1-1 1A17 17 0 0 1 3 4a1 1 0 0 1 1-1h3.5a1 1 0 0 1 1 1 11 11 0 0 0 .6 3.6 1 1 0 0 1-.25 1z" fill="#111"/></svg></div>
    <div><h4>PHONE NUMBER</h4><p>(08) 9400 3528</p></div>
  </div>
  <div class="abs info" style="top:532px">
    <div class="dot"><svg width="24" height="24" viewBox="0 0 24 24"><path d="M3 6h18v12H3z" fill="#111"/><path d="M3 6l9 7 9-7" stroke="#d8dc00" stroke-width="1.5" fill="none"/></svg></div>
    <div><h4>EMAIL ADDRESS</h4><p>hello@bluegumridge.example</p></div>
  </div>
  <div class="abs form">
    <div class="field" style="left:34px;top:38px;width:208px;height:45px"><i></i>First Name</div>
    <div class="field" style="left:250px;top:38px;width:208px;height:45px"><i></i>Last Name</div>
    <div class="field" style="left:34px;top:95px;width:424px;height:45px"><i></i>Email Address</div>
    <div class="field" style="left:34px;top:151px;width:424px;height:45px"><i></i>Phone Number</div>
    <div class="field" style="left:34px;top:206px;width:424px;height:85px"><i></i>Leave Message</div>
    <div class="submit">SUBMIT</div>
  </div>
</section>
<svg class="abs" style="left:0;top:3644px" width="1200" height="106" viewBox="0 0 1200 106">
  <defs><linearGradient id="fade" x1="0" x2="1"><stop offset="0" stop-color="#d8dc00" stop-opacity="0"/><stop offset=".3" stop-color="#d8dc00"/></linearGradient></defs>
  <polygon points="0,0 530,0 570,42 0,42" fill="url(#fade)"/>
  <polygon points="798,50 1200,50 1200,106 855,106" fill="#d8dc00"/>
  <polygon points="0,42 570,42 570,50 798,50 855,106 0,106" fill="#0b0b0b"/>
</svg>

<!-- Footer -->
<footer class="abs footer">
  <div class="abs brand-f"><div class="mark"></div><div class="name">BLUEGUM RIDGE</div></div>
  <div class="abs col" style="left:473px"><h5>QUICK LINKS</h5><ul><li>Home</li><li>About</li><li>Services</li><li>Blog</li><li>Contact Us</li></ul></div>
  <div class="abs col" style="left:688px"><h5>HELP LINKS</h5><ul><li>FAQ</li><li>Terms of use</li><li>Privacy Policy</li><li>Support Links</li><li>Conditions</li></ul></div>
  <div class="abs col" style="left:906px"><h5>CONTACT US</h5>
    <div class="fc"><span class="dot"></span><span>Bluegum Ridge<br>Western Australia</span></div>
    <div class="fc"><span class="dot"></span><span>+61 8 9400 1200</span></div>
    <div class="fc"><span class="dot"></span><span>office@bluegumridge.example</span></div>
  </div>
  <div class="abs rule"></div>
  <div class="abs copy">Copyrights2026.Bluegum Ridge.All Rights Reserved</div>
</footer>

</body>
</html>
```